Heron Loan Partners Business Card

We need a business card design for our mortgage servicing company. In addition to servicing the loans of homeowners, we help homeowners with purchasing their homes and any mortgage refinancing. We would like to see designs that use the colors in the logo attached below (gold-ish yellow and navy blue), and any other design you deem fit! The design should communicate a simpler life with smart mortgages provided by Heron.

```html
<!DOCTYPE html>
<html lang="en">
<head>
<meta charset="utf-8">
<title>Heron Loan Partners Business Card</title>
<link rel="stylesheet" href="https://fonts.googleapis.com/css2?family=Open+Sans:wght@400;600;700&display=swap">
<style>
  :root {
    --stage: #333333;
    --navy: #251f52;
    --gold: #dfb13c;
    --gold-deep: #c99a2a;
    --white: #ffffff;
  }
  * { box-sizing: border-box; margin: 0; padding: 0; }
  html, body { width: 1200px; height: 780px; overflow: hidden; }
  body {
    background: var(--stage);
    font-family: "Open Sans", Arial, sans-serif;
    position: relative;
  }
  .card {
    position: absolute;
    top: 235px;
    width: 540px;
    height: 310px;
    border-radius: 2px;
    box-shadow: 0 12px 30px rgba(0,0,0,0.45);
  }
  .card-back {
    left: 40px;
    background: var(--gold);
    overflow: hidden;
  }
  .back-pattern {
    position: absolute;
    inset: 0;
    background: linear-gradient(135deg, #e6bb48 0%, var(--gold) 50%, var(--gold-deep) 100%);
  }
  .back-name {
    position: absolute;
    right: 46px;
    top: 150px;
    font-weight: 700;
    font-size: 16px;
    color: var(--navy);
    display: flex;
    align-items: center;
    gap: 6px;
  }
  .back-name .dot {
    width: 8px; height: 8px; border-radius: 50%; background: var(--navy);
  }
  .card-front {
    left: 620px;
    background: var(--navy);
    border-bottom: 5px solid var(--gold);
    color: var(--white);
  }
  .brand {
    position: absolute;
    left: 40px;
    top: 56px;
    font-weight: 700;
    font-size: 30px;
    color: var(--white);
    letter-spacing: 0.5px;
  }
  .holder {
    position: absolute;
    left: 40px;
    top: 178px;
    font-weight: 700;
    font-size: 26px;
    letter-spacing: 1px;
  }
  .holder .first { color: var(--gold); }
  .holder .last { color: var(--white); }
  .holder .role {
    font-weight: 400;
    font-size: 15px;
    color: var(--gold);
    margin-left: 10px;
    vertical-align: 6px;
  }
  .contacts {
    position: absolute;
    left: 40px;
    right: 30px;
    top: 226px;
    font-size: 13px;
    line-height: 22px;
    letter-spacing: 0.3px;
  }
  .contacts .row { display: flex; gap: 26px; white-space: nowrap; }
  .contacts .label { color: var(--gold); font-weight: 600; }
</style>
</head>
<body>
  <section class="card card-back" aria-label="Card back">
    <div class="back-pattern" role="img" aria-label="Repeating brand pattern in gold tones"></div>
    <div class="back-name"><span class="dot"></span>Heron</div>
  </section>

  <section class="card card-front" aria-label="Card front">
    <div class="brand">Heron Loan Partners</div>
    <div class="holder">
      <span class="first">Dana</span> <span class="last">Whitlock</span><span class="role">CEO</span>
    </div>
    <div class="contacts">
      <div class="row">
        <span><span class="label">T:</span> (555) 014-2290</span>
        <span><span class="label">E:</span> info@heronloans.com</span>
        <span><span class="label">W:</span> www.heronloans.com</span>
      </div>
      <div class="row">
        <span>480 Lakeside Ave. Suite 300 Riverton, TX 75010</span>
      </div>
    </div>
  </section>
</body>
</html>
```